Bluetooth Earphone Packaging Design

We want to use the packaging for 4-5 of our Bluetooth Earphone series (Picture enclosed) and hence we would not like to put any product pictures on the packaging.

Material: E-Flute Paper box
Type: Window Box style
Design features we prefer: Colorful, creative, trendy, High tech.
Requirement: AI file is preferred
Size of Packaging: (L) 95 x (W) 40 x (H) 120 mm

Enclosed are a detailed description along with competitor designs for your reference.

Any further questions, please feel free to ask

```html
<!DOCTYPE html>
<html lang="en">
<head>
<meta charset="utf-8">
<title>Bluetooth Earphone 5.0 – Box Dieline</title>
<link href="https://fonts.googleapis.com/css2?family=Quicksand:wght@300;500;600&family=Open+Sans:wght@400;600;700&family=Oswald:wght@600&display=swap" rel="stylesheet">
<style>
  :root {
    --ink: #000000;
    --paper: #ffffff;
    --lime: #8cff0a;
    --backdrop: #edf0ee;
    --rule: #ffffff;
  }
  html, body {
    margin: 0;
    padding: 0;
    width: 1200px;
    height: 1200px;
    overflow: hidden;
    background: var(--backdrop);
  }
  .dieline {
    display: block;
    width: 1200px;
    height: 1200px;
  }
  .panel-ink { fill: var(--ink); }
  .panel-paper { fill: var(--paper); }
  .panel-lime { fill: var(--lime); }
  .bracket { fill: none; stroke-width: 1.2; }
  .bracket--light { stroke: var(--paper); }
  .bracket--dark { stroke: var(--ink); }
  .brand-name {
    font-family: "Quicksand", sans-serif;
    font-weight: 500;
    letter-spacing: 0.06em;
  }
  .headline-light {
    font-family: "Quicksand", sans-serif;
    font-weight: 300;
    letter-spacing: 0.03em;
  }
  .headline-bold {
    font-family: "Quicksand", sans-serif;
    font-weight: 600;
    letter-spacing: 0.03em;
  }
  .version {
    font-family: "Quicksand", sans-serif;
    font-weight: 500;
    fill: var(--lime);
  }
  .feature-label {
    font-family: "Oswald", sans-serif;
    font-weight: 600;
    font-size: 5.6px;
    fill: var(--ink);
    text-anchor: middle;
  }
  .powered-by {
    font-family: "Open Sans", sans-serif;
    font-weight: 600;
    font-size: 4.4px;
    fill: var(--paper);
    text-anchor: middle;
  }
  .partner-name {
    font-family: "Open Sans", sans-serif;
    font-weight: 700;
    font-size: 9.5px;
    fill: var(--paper);
  }
  .spec-heading {
    font-family: "Open Sans", sans-serif;
    font-weight: 700;
    font-size: 8.4px;
    fill: var(--lime);
  }
  .spec-row {
    font-family: "Open Sans", sans-serif;
    font-weight: 600;
    font-size: 6.8px;
    fill: var(--paper);
  }
  .caution-body {
    font-family: "Open Sans", sans-serif;
    font-weight: 600;
    font-size: 6.2px;
    fill: var(--paper);
  }
  .legal-note {
    font-family: "Open Sans", sans-serif;
    font-weight: 600;
    font-size: 5.4px;
    fill: var(--paper);
  }
  .legal-note .accent { fill: var(--lime); }
  .cert-mark { fill: none; stroke: var(--paper); stroke-width: 1.6; }
</style>
</head>
<body>
<svg class="dieline" viewBox="320 734 840 840" xmlns="http://www.w3.org/2000/svg" role="img" aria-label="Flat dieline of the Bluetooth Earphone 5.0 box">

  <!-- top closure flap -->
  <g class="top-flap">
    <path class="panel-ink" d="M455,1012 V848 Q455,833 470,833 H707 Q722,833 722,848 V1012 Z"/>
    <polygon class="panel-lime" points="355,955 452,955 452,1012 341,1012"/>
    <polygon class="panel-lime" points="727,955 822,955 837,1012 727,1012"/>
  </g>

  <!-- front panel -->
  <g class="front-panel">
    <rect class="panel-paper" x="455" y="1012" width="267" height="228"/>
    <path class="panel-ink" d="M500,1012 H678 L688,1075 Q690,1095 670,1095 H508 Q488,1095 490,1075 Z"/>
    <path class="bracket bracket--light" d="M527,1036 V1030 H534 M645,1030 H652 V1036 M527,1071 V1077 H534 M645,1077 H652 V1071"/>
    <text class="brand-name" x="589" y="1057" font-size="13.5" fill="var(--lime)" text-anchor="middle">Company Name</text>

    <text class="headline-light" x="492" y="1181" font-size="22" fill="var(--ink)">Bluetooth</text>
    <text class="headline-bold" x="492" y="1206" font-size="21" fill="var(--ink)">Earphone</text>
    <text class="version" x="608" y="1205" font-size="50">5.0</text>

    <rect class="panel-ink" x="455" y="1240" width="267" height="113"/>

    <g class="feature-badge">
      <polygon class="panel-lime" points="520,1240 543.4,1253.5 543.4,1280.5 520,1294 496.6,1280.5 496.6,1253.5"/>
      <circle cx="520" cy="1256" r="3.2" fill="var(--ink)"/>
      <text class="feature-label" x="520" y="1272">Bluetooth</text>
      <text class="feature-label" x="520" y="1279">5.0</text>
    </g>
    <g class="feature-badge">
      <polygon class="panel-lime" points="589,1240 612.4,1253.5 612.4,1280.5 589,1294 565.6,1280.5 565.6,1253.5"/>
      <path d="M584,1254 H587 L591,1251 V1261 L587,1258 H584 Z" fill="var(--ink)"/>
      <path d="M593,1253.5 Q595.5,1256 593,1258.5" fill="none" stroke="var(--ink)" stroke-width="0.8"/>
      <text class="feature-label" x="589" y="1272">Exceptional</text>
      <text class="feature-label" x="589" y="1279">Sound Quality</text>
    </g>
    <g class="feature-badge">
      <polygon class="panel-lime" points="658,1240 681.4,1253.5 681.4,1280.5 658,1294 634.6,1280.5 634.6,1253.5"/>
      <rect x="656" y="1250" width="4" height="7" rx="2" fill="var(--ink)"/>
      <path d="M654.5,1255.5 Q654.5,1259.5 658,1259.5 Q661.5,1259.5 661.5,1255.5 M658,1259.5 V1262" fill="none" stroke="var(--ink)" stroke-width="0.8"/>
      <text class="feature-label" x="658" y="1272">High Definition</text>
      <text class="feature-label" x="658" y="1279">Microphone</text>
    </g>

    <text class="powered-by" x="589" y="1316">POWERED BY</text>
    <circle cx="564" cy="1327" r="4" fill="var(--paper)"/>
    <text class="partner-name" x="571" y="1330.5">Linkwave</text>
  </g>

  <!-- bottom closure flap -->
  <path class="panel-ink bottom-flap" d="M455,1352 H722 V1475 H662 V1437 H516 V1475 H455 Z"/>

  <!-- left side panel -->
  <g class="side-panel side-panel--left">
    <rect class="panel-paper" x="341" y="1012" width="114" height="228"/>
    <polygon class="panel-lime" points="341,1240 455,1240 455,1425 396,1425 396,1405 369,1395 341,1395"/>
    <path class="bracket bracket--dark" d="M358,1266 V1262 H363 M432,1262 H437 V1266 M358,1286 V1290 H363 M432,1290 H437 V1286"/>
    <text class="brand-name" x="397" y="1278" font-size="8.4" fill="var(--ink)" text-anchor="middle">Company Name</text>
    <text class="headline-light" x="353" y="1319" font-size="10" fill="var(--ink)">Bluetooth</text>
    <text class="headline-bold" x="353" y="1331" font-size="9.6" fill="var(--ink)">Earphone</text>
    <text class="headline-light" x="406" y="1332" font-size="22" fill="var(--ink)">5.0</text>
  </g>

  <!-- right side panel -->
  <g class="side-panel side-panel--right">
    <rect class="panel-paper" x="722" y="1012" width="115" height="228"/>
    <rect class="panel-lime" x="722" y="1240" width="115" height="185"/>
    <text class="headline-light" transform="translate(791,1108) rotate(90)" font-size="23" fill="var(--ink)">Bluetooth</text>
    <text class="headline-bold" transform="translate(761,1108) rotate(90)" font-size="22.5" fill="var(--ink)">Earphone</text>
    <text class="headline-light" transform="translate(761,1252) rotate(90)" font-size="52" fill="var(--ink)">5.0</text>
  </g>

  <!-- back panel -->
  <g class="back-panel">
    <path class="panel-ink" d="M944,1012 V962 Q944,955 951,955 H993 Q1000,955 1000,962 V1012 Z"/>
    <path class="panel-ink" d="M837,1012 H1105 L1140,1035 V1335 L1043,1425 V1468 Q1043,1475 1036,1475 H910 Q903,1475 903,1468 V1425 L837,1350 Z"/>

    <text class="spec-heading" x="852" y="1034">Specification</text>
    <g class="spec-table">
      <text class="spec-row" x="852" y="1053">Bluetooth Version</text><text class="spec-row" x="976" y="1053">: 5.0</text>
      <text class="spec-row" x="852" y="1067">Wireless Playback Duration</text><text class="spec-row" x="976" y="1067">: 3 - 4 h</text>
      <text class="spec-row" x="852" y="1081">Standby Time</text><text class="spec-row" x="976" y="1081">: 80 h</text>
      <text class="spec-row" x="852" y="1095">Wireless Range</text><text class="spec-row" x="976" y="1095">: 10 m</text>
      <text class="spec-row" x="852" y="1110">Impedance</text><text class="spec-row" x="976" y="1110">: 32 Ω</text>
      <text class="spec-row" x="852" y="1124">Sound Pressure Level</text><text class="spec-row" x="976" y="1124">: 100dB ± 3dB</text>
      <text class="spec-row" x="852" y="1138">Frequency Response</text><text class="spec-row" x="976" y="1138">: 20 - 20kHz</text>
      <text class="spec-row" x="852" y="1152">Driver Unit</text><text class="spec-row" x="976" y="1152">: 10mm</text>
    </g>

    <text class="spec-heading" x="852" y="1172">Caution</text>
    <text class="caution-body" x="852" y="1186">Lorem ipsum dolor sit amet, consectetur adipiscing elit. Curabitur</text>
    <text class="caution-body" x="852" y="1197">dapibus vitae mauris consectetur fermentum. Pellentesque</text>
    <text class="caution-body" x="852" y="1208">eleifend vel orci non tristique.</text>

    <path class="bracket bracket--light" d="M852,1233 V1227 H859 M958,1227 H965 V1233 M852,1276 V1282 H859 M958,1282 H965 V1276"/>

    <g class="legal-note">
      <text x="979" y="1230"><tspan class="accent">© 2019 Lorem ipsum dolor sit amet,</tspan></text>
      <text x="979" y="1240.5">consectetur adipiscing elit. Curabitur</text>
      <text x="979" y="1251">dapibus vitae mauris consectetur</text>
      <text x="979" y="1261.5">fermentum. Pellentesque eleifend vel</text>
      <text x="979" y="1272">orci non tristique. Donec a orci luctus,</text>
      <text x="979" y="1282.5">bibendum leo a, hendrerit nunc.</text>
    </g>

    <line x1="852" y1="1298" x2="1093" y2="1298" stroke="var(--rule)" stroke-width="1"/>

    <g class="certification-marks">
      <rect class="cert-mark" x="853" y="1316" width="22" height="18" rx="2"/>
      <circle class="cert-mark" cx="898" cy="1325" r="9"/>
      <circle class="cert-mark" cx="918" cy="1325" r="9"/>
      <polygon class="cert-mark" points="950,1314 962,1335 938,1335"/>
      <circle class="cert-mark" cx="988" cy="1325" r="9"/>
      <rect class="cert-mark" x="1013" y="1315" width="16" height="20"/>
      <polygon class="cert-mark" points="1051,1314 1061,1333 1041,1333"/>
      <circle class="cert-mark" cx="1081" cy="1325" r="10"/>
    </g>
  </g>
</svg>
</body>
</html>
```